Business card for my new company (Accounting firm)

I need a business card for my new business Brightwell Advisory and Ledger SA. Our services are accounting, tax, audit and financial management. Our customers are small companies, start-ups and new companies. The final design has to show financial security, trust and growth. Please find our logo attached to the business card. Text for the business card: Brightwell Advisory and Ledger SA Tomas Varenholt Director and Founder Certified Accountant Tel. 022 418 57 34 tv@clairevalconseil.ch www.clairevalconseil.ch Rue des Vergières 27 1201 Geneva
Target Market(s)
Our customers are small companies, start-ups and new companies.
Industry/Entity Type
Finance And Accounting
Contact Information for Business Card
Claireval Conseil et Comptes SA
Tomas Varenholt
Directeur et Fondateur
Expert-comptable diplômé
Tél. 022 418 57 34
tv@clairevalconseil.ch
www.clairevalconseil.ch
Rue des Vergières 27
1201 Genève

```html
<!DOCTYPE html>
<html lang="fr">
<head>
<meta charset="utf-8">
<title>Claireval Conseil et Comptes SA – Carte de visite</title>
<link rel="stylesheet" href="https://fonts.googleapis.com/css2?family=Open+Sans:wght@400;600;700&display=swap">
<style>
  :root {
    --bg: #2b2b2d;
    --brand-blue: #33b0e0;
    --brand-deep: #1d6a9a;
    --paper: #ffffff;
    --ink: #3a3a3c;
    --ink-soft: #55575a;
    --rule: #2f2f31;
  }
  * { box-sizing: border-box; margin: 0; padding: 0; }
  html, body { width: 1200px; height: 960px; overflow: hidden; }
  body {
    background: var(--bg);
    font-family: "Open Sans", Arial, sans-serif;
    display: flex;
    flex-direction: column;
    align-items: center;
    justify-content: center;
    gap: 50px;
  }
  .card {
    width: 700px;
    height: 400px;
    position: relative;
    box-shadow: 0 10px 30px rgba(0,0,0,.45);
  }

  /* Back side */
  .card-back {
    background: var(--brand-blue);
    display: flex;
    flex-direction: column;
    align-items: center;
    justify-content: center;
    gap: 22px;
    color: var(--paper);
  }
  .back-wordmark {
    display: flex;
    align-items: center;
    gap: 16px;
    font-size: 46px;
    font-weight: 600;
    letter-spacing: 1px;
  }
  .back-wordmark .mark-square {
    width: 30px; height: 30px;
    background: var(--paper);
  }
  .back-url {
    font-size: 18px;
    letter-spacing: 4px;
  }

  /* Front side */
  .card-front {
    background: var(--paper);
    display: flex;
    align-items: center;
  }
  .front-brand {
    width: 290px;
    display: flex;
    align-items: center;
    justify-content: center;
    gap: 12px;
    color: var(--ink);
    font-size: 32px;
    font-weight: 600;
    letter-spacing: .5px;
  }
  .front-brand .mark-square {
    width: 22px; height: 22px;
    background: var(--brand-blue);
  }
  .divider {
    width: 1.5px;
    height: 200px;
    background: var(--rule);
  }
  .details {
    padding-left: 34px;
    color: var(--ink);
  }
  .person-name {
    color: var(--brand-blue);
    font-size: 27px;
    font-weight: 700;
    line-height: 1.1;
  }
  .person-role {
    font-size: 17px;
    line-height: 1.3;
    margin-top: 2px;
  }
  .address {
    font-size: 17px;
    line-height: 1.3;
    color: var(--ink-soft);
    margin-top: 16px;
  }
  .contact-list {
    list-style: none;
    margin-top: 14px;
    font-size: 17px;
    line-height: 1.35;
    color: var(--ink-soft);
  }
  .contact-list li {
    display: flex;
    align-items: center;
    gap: 10px;
  }
  .contact-list svg { width: 16px; height: 16px; flex: none; fill: var(--brand-blue); }
</style>
</head>
<body>

  <section class="card card-back" aria-label="Verso de la carte">
    <div class="back-wordmark"><span class="mark-square"></span><span>Claireval</span></div>
    <div class="back-url">www.clairevalconseil.ch</div>
  </section>

  <section class="card card-front" aria-label="Recto de la carte">
    <div class="front-brand"><span class="mark-square"></span><span>Claireval</span></div>
    <div class="divider"></div>
    <div class="details">
      <h1 class="person-name">Tomas Varenholt</h1>
      <p class="person-role">Directeur et Fondateur<br>Expert-comptable diplômé</p>
      <p class="address">Rue des Vergières 27<br>1201 Genève</p>
      <ul class="contact-list">
        <li>
          <svg viewBox="0 0 24 24" aria-hidden="true"><path d="M6.6 10.8a15.1 15.1 0 0 0 6.6 6.6l2.2-2.2a1 1 0 0 1 1-.25 11.4 11.4 0 0 0 3.6.57 1 1 0 0 1 1 1V20a1 1 0 0 1-1 1A17 17 0 0 1 3 4a1 1 0 0 1 1-1h3.5a1 1 0 0 1 1 1c0 1.25.2 2.45.57 3.57a1 1 0 0 1-.25 1z"/></svg>
          022 418 57 34
        </li>
        <li>
          <svg viewBox="0 0 24 24" aria-hidden="true"><path d="M2 5h20v14H2zm2 2v.5l8 5 8-5V7zm0 2.8V17h16V9.8l-8 5z"/></svg>
          tv@clairevalconseil.ch
        </li>
        <li>
          <svg viewBox="0 0 24 24" aria-hidden="true"><path d="M12 2a10 10 0 1 0 0 20 10 10 0 0 0 0-20zm6.9 9h-3a15 15 0 0 0-1.3-5.6A8 8 0 0 1 18.9 11zM12 4.1c.9 1.2 1.8 3.6 1.9 6.9h-3.8C10.2 7.7 11.1 5.3 12 4.1zM9.4 5.4A15 15 0 0 0 8.1 11h-3a8 8 0 0 1 4.3-5.6zM5.1 13h3a15 15 0 0 0 1.3 5.6A8 8 0 0 1 5.1 13zm6.9 6.9c-.9-1.2-1.8-3.6-1.9-6.9h3.8c-.1 3.3-1 5.7-1.9 6.9zm2.6-1.3a15 15 0 0 0 1.3-5.6h3a8 8 0 0 1-4.3 5.6z"/></svg>
          www.clairevalconseil.ch
        </li>
      </ul>
    </div>
  </section>

</body>
</html>
```